New Business Card Design Project LORVANTI-Italy

we are LORVANTI-Italy
our company in the market for 3 years we are luxury cosmetic company and its about time for a facelift :)
i will like to have elegant luxurious and unique business card
that will give the person that get it a unique, luxurious and elegant impression
I'm VERY OPEN FOR NEW IDEAS , even duo i add a few files of things that i see on line and i like them

i add my logo as well
my website is LORVANTI.COM
(if you would like to see the main style that we have)

Target Market(s)

adult that have money :)

Industry/Entity Type

Business

Contact Information for Business Card

Name - Dario Lorvanti
Position - CEO and CO Founder
address - 4817 E Halvern
telephone - 555-384-1926
email - dario@lorvanti.com
fax - 555-384-1926
website - LORVANTI.COM

Colors
000000
959595
fbee3e
ffffff

Requirements
Must have
• big logo in GOLD color
• elegant look
• impressive
Nice to have
• not must but maybe classy pattern background
• not must but maybe emblem
• maybe clear plastic business card
Should not have
• colors
• images

```html
<!DOCTYPE html>
<html lang="en">
<head>
<meta charset="UTF-8">
<title>Dario Lorvanti – Business Card</title>
<link rel="stylesheet" href="https://fonts.googleapis.com/css2?family=Oswald:wght@300;400;600&family=Roboto+Condensed:wght@300;400&display=swap">
<style>
  :root {
    --stage-bg: #2d3f46;
    --card-bg: #2a2420;
    --card-bg-light: #332c27;
    --gold: #d6b45e;
    --gold-soft: #c9a752;
  }
  * { box-sizing: border-box; margin: 0; padding: 0; }
  html, body {
    width: 1200px;
    height: 900px;
    overflow: hidden;
    background: var(--stage-bg);
  }
  .stage {
    position: relative;
    width: 1200px;
    height: 900px;
  }
  .business-card {
    position: absolute;
    left: 345px;
    top: 40px;
    width: 510px;
    height: 820px;
    background: var(--card-bg);
    overflow: hidden;
    box-shadow: 0 18px 40px rgba(0,0,0,0.35);
  }
  .card-pattern {
    position: absolute;
    inset: 0;
    background: radial-gradient(ellipse at 50% 40%, var(--card-bg-light) 0%, var(--card-bg) 75%);
  }
  .card-content {
    position: absolute;
    left: 50%;
    top: 50%;
    width: 820px;
    height: 510px;
    transform: translate(-50%, -50%) rotate(-90deg);
    display: flex;
    flex-direction: column;
    align-items: center;
    justify-content: center;
    color: var(--gold);
    text-align: center;
  }
  .brand-mark {
    display: flex;
    align-items: center;
    gap: 16px;
    height: 130px;
    margin-bottom: 22px;
  }
  .brand-dot {
    width: 26px;
    height: 26px;
    border-radius: 50%;
    background: var(--gold);
  }
  .brand-name {
    font-family: 'Oswald', sans-serif;
    font-weight: 600;
    font-size: 54px;
    letter-spacing: 6px;
    color: var(--gold);
  }
  .person-name {
    font-family: 'Oswald', sans-serif;
    font-weight: 600;
    font-size: 40px;
    line-height: 1;
    letter-spacing: 0.5px;
    text-transform: uppercase;
  }
  .person-title {
    font-family: 'Roboto Condensed', sans-serif;
    font-weight: 300;
    font-size: 24px;
    line-height: 1.2;
    margin-top: 4px;
    margin-bottom: 14px;
    color: var(--gold-soft);
  }
  .contact-list {
    list-style: none;
    display: flex;
    flex-direction: column;
    align-items: center;
  }
  .contact-item {
    display: flex;
    flex-direction: column;
    align-items: center;
    font-family: 'Roboto Condensed', sans-serif;
    font-weight: 300;
    font-size: 17px;
    line-height: 1.2;
    color: var(--gold-soft);
  }
  .contact-item::before {
    content: "";
    width: 9px;
    height: 9px;
    background: var(--gold);
    margin: 4px 0 3px;
  }
  .contact-item.is-site {
    font-size: 19px;
  }
  .address {
    margin-top: 22px;
    font-family: 'Roboto Condensed', sans-serif;
    font-weight: 300;
    font-size: 20px;
    color: var(--gold-soft);
  }
</style>
</head>
<body>
  <main class="stage">
    <section class="business-card">
      <div class="card-pattern" role="img" aria-label="Fine diamond lattice pattern in dark brown tones"></div>
      <div class="card-content">
        <div class="brand-mark">
          <span class="brand-dot"></span>
          <span class="brand-name">LORVANTI</span>
        </div>
        <h1 class="person-name">Dario Lorvanti</h1>
        <p class="person-title">CEO and CO Founder</p>
        <ul class="contact-list">
          <li class="contact-item">555-384-1926</li>
          <li class="contact-item">555-384-1926</li>
          <li class="contact-item">dario@lorvanti.com</li>
          <li class="contact-item is-site">LORVANTI.COM</li>
        </ul>
        <p class="address">4817 E Halvern</p>
      </div>
    </section>
  </main>
</body>
</html>
```